Upstart Retirement Planning Firm needs help with business card design

Harborview Nest Advisors, LLC is looking for help with business card design. We give advice on investments, insurance, and other financial matters related to retirement. There are some required disclosures that we will provide but mostly we are looking for a professional, classy business card that reflects the theme we have chosen. We have a logo that is attached but we would like to add a phrase; "Turning Your Earned Income Into Retirement Income"

Doubled sided only so that we can add the required disclosures (needed for our industry) on the back of the card. We will provide the exact words for this in 1-2 days.

Target Market(s)

Retirees and Pre-retirees. Professionals 50+ years old

Industry/Entity Type

Financial Planning

Contact Information for Business Card

We currently have two people who will need separate cards so we'd like to have a template so that we can add names for new cards in the future.

For the first run, please show the following information.

Gregor Pelham, MBA, ChFC®, CLU®
Financial Advisor, Registered Representative
gpelham@harborviewnest.example
Phone: (555) 318-2946
Toll Free Fax: (800) 555-0193

Address is
2187 Meadowlark Ridge Rd.
Suite K418
Virginia Beach, VA 23999

Colors
3277b5

Requirements
Must have
• Logo, contact info, small phase to describe business (in description), required legal disclosures on back of the card as follows (in small font)
• Gregor Pelham is a registered representative of and offers securities through Brightmoor Capital Brokerage Corporation, Member FNQX. Brightmoor Capital Brokerage Corporation is a member of the Brightmoor Capital Alliance which is the marketing name for Brightmoor Holding Corporation and its affiliates.
Nice to have
• Rounded edges, raised letters
Should not have
• any colors that aren't in the logo (other than black for font)

```html
<!DOCTYPE html>
<html lang="en">
<head>
<meta charset="utf-8">
<title>Harborview Nest Advisors – Business Card</title>
<link rel="stylesheet" href="https://fonts.googleapis.com/css2?family=Old+Standard+TT:wght@400;700&display=swap">
<style>
  :root {
    --brand-blue: #0d6ab4;
    --brand-grey: #ababab;
    --paper: #ffffff;
    --ink: #2b2b2b;
    --backdrop: #e4e4e4;
    --serif: "Old Standard TT", Georgia, serif;
  }
  * { box-sizing: border-box; margin: 0; padding: 0; }
  html, body {
    width: 1189px; height: 1200px; overflow: hidden;
    background: var(--backdrop);
    font-family: var(--serif);
  }
  .card {
    position: absolute; left: 140px; width: 917px; height: 524px;
    box-shadow: 0 3px 10px rgba(0,0,0,.25);
    overflow: hidden;
  }
  .card--front { top: 45px; background: var(--paper); }
  .card--back  { top: 624px; height: 523px; background: var(--brand-grey); color: var(--paper); }

  /* brand block */
  .brand { position: absolute; left: 0; right: 0; text-align: center; }
  .brand__name {
    font-weight: 400; letter-spacing: 2px; text-transform: uppercase;
    white-space: nowrap; line-height: 1;
  }
  .brand__tagline {
    display: flex; align-items: center; justify-content: center; gap: 16px;
    margin: 0 auto; font-size: 15px; letter-spacing: 1.5px; white-space: nowrap;
  }
  .brand__tagline::before, .brand__tagline::after {
    content: ""; flex: 1; height: 1px; background: currentColor;
  }

  .card--front .brand { top: 110px; }
  .card--front .brand__name { font-size: 38px; color: var(--ink); }
  .card--front .brand__tagline { width: 560px; margin-top: 44px; color: var(--ink); }

  .card--back .brand { top: 150px; }
  .card--back .brand__name { font-size: 46px; }
  .card--back .brand__tagline { width: 720px; margin-top: 44px; font-size: 18px; }

  .disclosure {
    position: absolute; left: 90px; right: 90px; bottom: 40px;
    font-size: 12.5px; line-height: 1.5; text-align: center;
  }

  /* front contact area */
  .rule-line {
    position: absolute; left: 0; right: 0; top: 255px; height: 3px;
    background: var(--brand-blue);
  }
  .contact-band {
    position: absolute; left: 0; right: 0; top: 268px; bottom: 0;
    background: var(--brand-blue); color: var(--paper);
  }
  .person { position: absolute; left: 35px; top: 62px; }
  .person__name { font-size: 42px; font-weight: 700; line-height: 1; }
  .person__creds { font-size: 19px; font-weight: 700; margin-top: 6px; }
  .person__title { font-size: 23px; font-weight: 700; line-height: 1.3; margin-top: 12px; }

  .divider {
    position: absolute; left: 375px; top: 30px; width: 1px; height: 200px;
    background: rgba(255,255,255,.6);
  }
  .contact-list { position: absolute; left: 411px; top: 46px; list-style: none; }
  .contact-list li {
    display: flex; align-items: flex-start; gap: 13px;
    font-size: 23px; font-weight: 700; line-height: 1.22; margin-bottom: 9px;
  }
  .contact-list svg { flex: none; width: 14px; height: 14px; margin-top: 7px; }
</style>
</head>
<body>

<section class="card card--front">
  <div class="brand">
    <div class="brand__name">Harborview Nest Advisors, LLC</div>
    <div class="brand__tagline">Turning Your Earned Income Into Retirement Income</div>
  </div>
  <div class="rule-line"></div>

  <div class="contact-band">
    <div class="person">
      <div class="person__name">Gregor Pelham</div>
      <div class="person__creds">MBA, ChFC®, CLU®</div>
      <div class="person__title">Financial Advisor,<br>Registered Representative</div>
    </div>

    <div class="divider"></div>

    <ul class="contact-list">
      <li>
        <svg viewBox="0 0 14 14" aria-hidden="true"><rect width="14" height="14" fill="#fff"/><path d="M4 3h2l1 2.5-1.2.8a5 5 0 0 0 2 2l.8-1.2L11 8v2c0 .6-.5 1-1 1A7 7 0 0 1 3 4c0-.5.4-1 1-1z" fill="#0d6ab4"/></svg>
        (555) 318-2946
      </li>
      <li>
        <svg viewBox="0 0 14 14" aria-hidden="true"><rect width="14" height="14" fill="#fff"/><rect x="3" y="5" width="8" height="5" fill="#0d6ab4"/><rect x="4.5" y="3" width="5" height="2" fill="#0d6ab4"/><rect x="4.5" y="7" width="5" height="1" fill="#fff"/></svg>
        (800) 555-0193
      </li>
      <li>
        <svg viewBox="0 0 14 14" aria-hidden="true"><rect width="14" height="14" fill="#fff"/><rect x="3" y="4" width="8" height="6" fill="#0d6ab4"/><path d="M3 4l4 3.2L11 4" stroke="#fff" fill="none"/></svg>
        gpelham@harborviewnest.example
      </li>
      <li>
        <svg viewBox="0 0 14 14" aria-hidden="true"><rect width="14" height="14" fill="#fff"/><path d="M7 2.5a3 3 0 0 1 3 3c0 2.2-3 5.5-3 5.5S4 7.7 4 5.5a3 3 0 0 1 3-3z" fill="#0d6ab4"/><circle cx="7" cy="5.5" r="1" fill="#fff"/></svg>
        <span>2187 Meadowlark Ridge Rd. Suite K418<br>Virginia Beach, VA 23999</span>
      </li>
    </ul>
  </div>
</section>

<section class="card card--back">
  <div class="brand">
    <div class="brand__name">Harborview Nest Advisors, LLC</div>
    <div class="brand__tagline">Turning Your Earned Income Into Retirement Income</div>
  </div>
  <p class="disclosure">
    Gregor Pelham is a registered representative of and offers securities through Brightmoor Capital Brokerage Corporation, Member FNQX.
    Brightmoor Capital Brokerage Corporation is a member of the Brightmoor Capital Alliance which is the marketing name for
    Brightmoor Holding Corporation and its affiliates.
  </p>
</section>

</body>
</html>
```